Business Card design for law firm = Brightvale Australia

We are seeking a new design for our business cards.
We are keeping our logo, which is attached.
We need space for
Name
Title
Address is , which is
Level 7
214 Marlowe Street
Sydney NSW 2047
Phone :
Mobile :
Fax :
Email :
DX :
website www.brightvale-example.com.au

Industry/Entity Type

Law Firm / Banking and Finance

Contact Information for Business Card

We are seeking a new design for our business cards. We are keeping our logo. We need space for Name Title Address is Level 7 214 Marlowe Street Sydney NSW 2047 Phone Mobile Fax Email DX website www.brightvale-example.com.au

Colors
0054AA
0677BA
7BADD7
CADEEF
E8F1F8

Requirements
Must have
• see our website for general feel www.brightvale-example.com.au

```html
<!DOCTYPE html>
<html lang="en">
<head>
<meta charset="utf-8">
<title>Brightvale Australia – Business Card</title>
<link rel="stylesheet" href="https://fonts.googleapis.com/css2?family=Montserrat:wght@400;500;700&display=swap">
<style>
  :root {
    --backdrop: #637a86;
    --card: #ffffff;
    --navy: #0054aa;
    --blue: #0677ba;
    --sky: #7badd7;
    --ink: #1d1d1f;
  }
  * { box-sizing: border-box; margin: 0; padding: 0; }
  html, body { width: 1200px; height: 1000px; overflow: hidden; }
  body {
    background: var(--backdrop);
    font-family: "Montserrat", Arial, sans-serif;
    color: var(--ink);
    position: relative;
  }
  .card {
    position: absolute;
    top: 347px;
    width: 500px;
    height: 306px;
    background: var(--card);
    box-shadow: 0 10px 24px rgba(0, 0, 0, 0.25);
  }
  .card--front { left: 60px; }
  .card--back { left: 640px; }

  .brand {
    position: absolute;
    display: flex;
    align-items: center;
    gap: 14px;
  }
  .brand__square {
    width: 54px;
    height: 54px;
    background: var(--blue);
  }
  .brand__name {
    font-size: 34px;
    font-weight: 500;
    color: var(--navy);
    letter-spacing: 0.2px;
  }
  .card--front .brand { left: 120px; top: 126px; }
  .card--back .brand { right: 30px; top: 36px; }
  .card--back .brand__square { width: 44px; height: 44px; }
  .card--back .brand__name { font-size: 28px; }

  .person {
    position: absolute;
    left: 34px;
    top: 110px;
  }
  .person__name {
    font-size: 24px;
    font-weight: 700;
    color: var(--blue);
    line-height: 1;
  }
  .person__title {
    font-size: 9px;
    font-weight: 500;
    letter-spacing: 0.4px;
    margin-top: 4px;
    padding-bottom: 6px;
    border-bottom: 1.5px solid var(--blue);
    width: 170px;
  }
  .person__address {
    font-size: 11px;
    line-height: 1.45;
    margin-top: 7px;
  }
  .contacts {
    position: absolute;
    left: 34px;
    top: 198px;
    list-style: none;
  }
  .contacts__item {
    display: flex;
    align-items: center;
    gap: 9px;
    font-size: 11px;
    height: 18px;
  }
  .contacts__icon {
    width: 12px;
    height: 12px;
    flex: none;
    color: var(--blue);
  }
  .contacts__label {
    width: 12px;
    flex: none;
    font-size: 9px;
    font-weight: 700;
    color: var(--blue);
  }
</style>
</head>
<body>
  <section class="card card--front" aria-label="Card front">
    <div class="brand">
      <span class="brand__square"></span>
      <span class="brand__name">Brightvale</span>
    </div>
  </section>

  <section class="card card--back" aria-label="Card back">
    <div class="brand">
      <span class="brand__square"></span>
      <span class="brand__name">Brightvale</span>
    </div>

    <div class="person">
      <p class="person__name">NAME</p>
      <p class="person__title">MANAGING DIRECTOR</p>
      <p class="person__address">Level 7, 214 Marlowe Street<br>Sydney NSW 2047</p>
    </div>

    <ul class="contacts">
      <li class="contacts__item">
        <svg class="contacts__icon" viewBox="0 0 12 12" aria-hidden="true"><circle cx="6" cy="6" r="6" fill="currentColor"/><path d="M4 3.2l1.2 1.4-.6.8a4 4 0 0 0 2 2l.8-.6L8.8 8 8 8.9C5.6 8.6 3.4 6.4 3.1 4z" fill="#fff"/></svg>
        <span>02 9000 4182</span>
      </li>
      <li class="contacts__item">
        <svg class="contacts__icon" viewBox="0 0 12 12" aria-hidden="true"><rect x="3" y="1" width="6" height="3" fill="currentColor"/><rect x="1" y="4" width="10" height="5" rx="1" fill="currentColor"/><rect x="3" y="7.5" width="6" height="3.5" fill="currentColor" stroke="#fff" stroke-width=".8"/></svg>
        <span>02 9000 4183</span>
      </li>
      <li class="contacts__item">
        <svg class="contacts__icon" viewBox="0 0 12 12" aria-hidden="true"><rect x="0.5" y="2.5" width="11" height="7.5" fill="currentColor"/><path d="M.8 2.8L6 7l5.2-4.2" fill="none" stroke="#fff" stroke-width=".9"/></svg>
        <span>enquiries@brightvale-example.com.au</span>
      </li>
      <li class="contacts__item">
        <span class="contacts__label">DX</span>
        <span>318 Sydney</span>
      </li>
      <li class="contacts__item">
        <svg class="contacts__icon" viewBox="0 0 12 12" aria-hidden="true"><g fill="none" stroke="currentColor" stroke-width="1"><circle cx="6" cy="6" r="5.2"/><ellipse cx="6" cy="6" rx="2.3" ry="5.2"/><path d="M.8 6h10.4M1.6 3.4h8.8M1.6 8.6h8.8"/></g></svg>
        <span>www.brightvale-example.com.au</span>
      </li>
    </ul>
  </section>
</body>
</html>
```